Brightway Haus Inc. Business Card Design

Brightway Haus Inc. is in search of a great clean design for our business cards!

Looking to incorporate our full logo and watermark on side one (however, I am open to having the text and watermark separated within the design.)

On side two, I am looking to have contact information (Name, Position, Phone #, Email, Website (www.thebrightwayhaus.ca). Can have the logo and/or watermark as part of the design if applicable.

Please add tagline "Where Shine Counts" on either side 1 or 2. This tagline can be in a sans serif, serif or cursive font as long as it compliments overall design. Capitalization can be title or sentence case depending on how it fits within the design.

Get creative!! Looking for a clean, crisp, premium design! Looking for a glossy card finish with spot UV features when printed. Cards will also be printed with rounded corners. Standard dimensions (3.5 x 2).

Target Market(s)

B2B - primary clients are business owners or property management corporations. (residential jobs are few and far between)

Industry/Entity Type

Business

Contact Information for Business Card

- clean, crisp design
- double sided
- spot UV accents and glossy finish upon printing
- standard business card size (3.5 x 2) with rounded corners
- please see project description for requirements per side

Font styles to use
Sans Serif

Requirements
Must have
• - adequate bleeds with print ready files
• - cohesive design elements between side 1 & 2
• - spot UV elements (can be on both sides or just one, use your discretion)
• - colour pallet should match the logo file provided
• - incorporate tagline "where shine counts" (this tagline can be in a serif or sans serif font as long as it is complimentary to the overall design.
Nice to have
• - Premium elements with a clean design
Should not have
• - Please omit cartoon or whimsical like designs, think premium.
• - Colours should not stray from the pallet of the provided logo.

```html
<!DOCTYPE html>
<html lang="en">
<head>
<meta charset="utf-8">
<title>Brightway Haus Inc. Business Card</title>
<link rel="stylesheet" href="https://fonts.googleapis.com/css2?family=Roboto:wght@400;700;900&family=Montserrat:wght@500&display=swap">
<style>
  :root {
    --backdrop: #3a3a3c;
    --card: #1f1f21;
    --gloss: #2c2c2e;
    --teal: #00a9b3;
    --silver: #a7a9ac;
    --text-light: #d4d5d7;
    --white: #ffffff;
  }
  html, body {
    margin: 0;
    padding: 0;
    width: 799px;
    height: 1200px;
    overflow: hidden;
    background: var(--backdrop);
    font-family: "Roboto", Arial, sans-serif;
  }
  .canvas {
    position: relative;
    width: 799px;
    height: 1200px;
  }
  .card {
    position: absolute;
    left: 60px;
    width: 680px;
    height: 389px;
    background: var(--card);
    border-radius: 14px;
    overflow: hidden;
    box-shadow: 0 18px 40px rgba(0,0,0,.45);
  }
  .card-front { top: 110px; }
  .card-back { top: 690px; }

  /* Front: spot UV brand mark */
  .front-mark {
    position: absolute;
    inset: 0;
    display: flex;
    align-items: center;
    justify-content: center;
    gap: 18px;
  }
  .front-mark .mark-square {
    width: 70px;
    height: 70px;
    background: var(--gloss);
  }
  .front-mark .mark-name {
    font-weight: 900;
    font-size: 38px;
    letter-spacing: 1px;
    color: var(--gloss);
    text-transform: uppercase;
  }

  /* Back: contact side */
  .brand {
    position: absolute;
    left: 40px;
    top: 38px;
    display: flex;
    align-items: center;
    gap: 14px;
  }
  .brand .brand-square {
    width: 44px;
    height: 44px;
    background: var(--teal);
  }
  .brand .brand-name {
    font-weight: 900;
    font-size: 40px;
    letter-spacing: -0.5px;
    color: var(--teal);
    text-transform: uppercase;
  }
  .identity {
    position: absolute;
    left: 40px;
    top: 118px;
    display: flex;
    align-items: center;
  }
  .person-name {
    font-weight: 700;
    font-size: 24px;
    color: var(--teal);
    padding-right: 12px;
    border-right: 1px solid var(--silver);
  }
  .person-role {
    font-size: 15px;
    color: var(--text-light);
    padding-left: 12px;
  }
  .contacts {
    position: absolute;
    left: 40px;
    top: 162px;
    margin: 0;
    padding: 0;
    list-style: none;
    font-size: 15px;
    color: var(--text-light);
    line-height: 22px;
  }
  .contacts li {
    display: flex;
    align-items: center;
    gap: 8px;
  }
  .contacts li.address { padding-left: 0; }
  .contacts svg {
    width: 13px;
    height: 13px;
    fill: var(--teal);
    flex: none;
  }
  .contacts .icon-gap { width: 13px; flex: none; }
  .contacts .accent { color: var(--teal); }
  .swoosh {
    position: absolute;
    left: 0;
    bottom: 0;
    width: 680px;
    height: 180px;
  }
  .tagline {
    position: absolute;
    right: 40px;
    bottom: 34px;
    margin: 0;
    font-family: "Montserrat", Arial, sans-serif;
    font-weight: 500;
    font-size: 19px;
    line-height: 26px;
    letter-spacing: 2.5px;
    color: var(--white);
    text-align: right;
    text-transform: uppercase;
  }
</style>
</head>
<body>
<main class="canvas">

  <section class="card card-front" aria-label="Card front">
    <div class="front-mark">
      <span class="mark-square"></span>
      <span class="mark-name">Brightway Haus Inc.</span>
    </div>
  </section>

  <section class="card card-back" aria-label="Card back">
    <div class="brand">
      <span class="brand-square"></span>
      <span class="brand-name">Brightway Haus Inc.</span>
    </div>

    <div class="identity">
      <span class="person-name">Morgan Hale</span>
      <span class="person-role">Managing Director</span>
    </div>

    <ul class="contacts">
      <li class="address"><span class="icon-gap"></span>48 Lakeview Avenue, Halton, Canada</li>
      <li>
        <svg viewBox="0 0 16 16" aria-hidden="true"><path d="M3 1h3l1.5 4-2 1.2a9 9 0 0 0 4.3 4.3L11 8.5l4 1.5v3a2 2 0 0 1-2 2A12 12 0 0 1 1 3a2 2 0 0 1 2-2z"/></svg>
        1800-555-0199
      </li>
      <li>
        <svg viewBox="0 0 16 16" aria-hidden="true"><path d="M1 3h14v10H1z M1 3l7 6 7-6" fill="none" stroke="#00a9b3" stroke-width="1.6"/></svg>
        morgan@thebrightwayhaus.ca
      </li>
      <li>
        <svg viewBox="0 0 16 16" aria-hidden="true"><circle cx="8" cy="8" r="6.5" fill="none" stroke="#00a9b3" stroke-width="1.5"/><path d="M1.5 8h13M8 1.5c-3 3.5-3 9.5 0 13M8 1.5c3 3.5 3 9.5 0 13" fill="none" stroke="#00a9b3" stroke-width="1.2"/></svg>
        www.<span class="accent">thebrightwayhaus</span>.ca
      </li>
    </ul>

    <svg class="swoosh" viewBox="0 0 680 180" preserveAspectRatio="none" aria-hidden="true">
      <path d="M0 20 C 120 70, 300 95, 460 85 C 560 78, 630 60, 680 45 L680 62 C 620 82, 540 100, 450 104 C 290 112, 120 88, 0 40 Z" fill="var(--silver)"/>
      <path d="M0 52 C 140 110, 320 125, 470 112 C 570 103, 640 88, 680 76 L680 180 L0 180 Z" fill="var(--teal)"/>
      <path d="M0 48 C 140 105, 320 120, 470 108 C 570 100, 640 85, 680 72" fill="none" stroke="var(--card)" stroke-width="3"/>
    </svg>

    <p class="tagline">Where<br>Shine Counts</p>
  </section>

</main>
</body>
</html>
```